Copper Lantern

Need a business card for our restaurant. Restaurant and Bar in the mountains of North Idaho. Rustic looking card

rustic design, wood and metal looking, primarily neutral colors

• Name, address, phone number, website, email address

```html
<!DOCTYPE html>
<html lang="en">
<head>
<meta charset="UTF-8">
<title>Copper Lantern — Business Card</title>
<link href="https://fonts.googleapis.com/css2?family=Montserrat:wght@400;500;800&display=swap" rel="stylesheet">
<style>
  :root {
    --stage: #2b2b2b;
    --card-dark: #161616;
    --card-light: #ffffff;
    --ink: #111111;
    --ink-soft: #2a2a2a;
    --paper: #ffffff;
  }
  * { box-sizing: border-box; margin: 0; padding: 0; }
  html, body { width: 1200px; height: 875px; overflow: hidden; }
  body {
    background: var(--stage);
    font-family: "Montserrat", sans-serif;
    display: flex;
    align-items: center;
    justify-content: center;
    gap: 40px;
  }
  .card {
    width: 540px;
    height: 309px;
    border-radius: 16px;
    position: relative;
    box-shadow: 0 18px 40px rgba(0,0,0,0.45);
  }
  .card--front {
    background: var(--card-dark);
    display: flex;
    align-items: center;
    justify-content: center;
  }
  .brand {
    display: flex;
    align-items: center;
    gap: 12px;
    font-weight: 500;
    letter-spacing: 0.18em;
    text-transform: uppercase;
  }
  .brand__dot {
    width: 14px; height: 14px;
    border-radius: 50%;
    flex: none;
  }
  .card--front .brand { color: var(--paper); font-size: 24px; }
  .card--front .brand__dot { border: 2px solid var(--paper); }

  .card--back { background: var(--card-light); color: var(--ink); }
  .card--back .brand {
    position: absolute;
    top: 34px; right: 34px;
    color: var(--ink);
    font-size: 13px;
  }
  .card--back .brand__dot { border: 2px solid var(--ink); width: 10px; height: 10px; }

  .person { position: absolute; left: 44px; top: 128px; }
  .person__name { font-weight: 800; font-size: 22px; line-height: 1.1; }
  .person__role { font-size: 12px; color: var(--ink-soft); margin-top: 2px; }

  .address {
    position: absolute;
    right: 44px; top: 128px;
    font-size: 12px;
    line-height: 1.35;
    text-align: right;
    color: var(--ink-soft);
  }

  .contacts {
    position: absolute;
    left: 44px; bottom: 34px;
    list-style: none;
    font-size: 13px;
    color: var(--ink-soft);
  }
  .contacts li { display: flex; align-items: center; gap: 8px; line-height: 1.6; }
  .contacts svg { width: 12px; height: 12px; fill: var(--ink); flex: none; }
</style>
</head>
<body>
  <section class="card card--front">
    <div class="brand"><span class="brand__dot"></span>Copper Lantern</div>
  </section>

  <section class="card card--back">
    <div class="brand"><span class="brand__dot"></span>Copper Lantern</div>

    <div class="person">
      <div class="person__name">Evan Marsh</div>
      <div class="person__role">Managing Director</div>
    </div>

    <address class="address">48 Timber Lane,<br>Pine Hollow, USA</address>

    <ul class="contacts">
      <li>
        <svg viewBox="0 0 24 24" aria-hidden="true"><path d="M6.6 10.8a15 15 0 0 0 6.6 6.6l2.2-2.2a1 1 0 0 1 1-.25 11.4 11.4 0 0 0 3.6.57 1 1 0 0 1 1 1V20a1 1 0 0 1-1 1A17 17 0 0 1 3 4a1 1 0 0 1 1-1h3.5a1 1 0 0 1 1 1c0 1.25.2 2.45.57 3.6a1 1 0 0 1-.25 1z"/></svg>
        (08) 4410 2286
      </li>
      <li>
        <svg viewBox="0 0 24 24" aria-hidden="true"><path d="M2 5h20v14H2z M2 5l10 8 10-8" fill="none" stroke="currentColor"/><path d="M2 5h20v2l-10 7L2 7z"/><path d="M2 9l10 7 10-7v10H2z"/></svg>
        hello@copperlantern.com
      </li>
      <li>
        <svg viewBox="0 0 24 24" aria-hidden="true"><circle cx="12" cy="12" r="10"/></svg>
        www.copperlantern.com
      </li>
    </ul>
  </section>
</body>
</html>
```